National Mission Critical Construction Contractor needs Stationery Design to make a bold statement

We are a small commercial construction company, working primarily in mission critical facilities across the U.S.. We have exciting corporate changes going an and a new logo and office space so we need new stationery. The final design should incorporate our new logo and invoke a fresh, high-tech feel while looking simple and modern.

Industry/Entity Type

Construction

Contact Information for Business Card

We are required to list our state licensing qualifications on the back of our card.

Font styles to use
Sans Serif

Requirements
Must have
• We need to have a design for second page of stationery, envelopes both standard and with a window and for a 3 x 4 notepad.

```html
<!DOCTYPE html>
<html lang="en">
<head>
<meta charset="utf-8">
<title>Northgate Construction Management – Business Card</title>
<link href="https://fonts.googleapis.com/css2?family=Open+Sans:wght@400;600&display=swap" rel="stylesheet">
<style>
  :root {
    --stage: #353535;
    --card-white: #fbfbfb;
    --brand-blue: #1565b8;
    --accent-blue: #2a86d6;
    --pattern-blue: #1a6cbf;
    --text-grey: #4a4a4a;
    --rule-grey: #cfcfcf;
    --white: #ffffff;
  }
  * { margin: 0; padding: 0; box-sizing: border-box; }
  html, body {
    width: 1200px; height: 750px; overflow: hidden;
    background: var(--stage);
    font-family: "Open Sans", Arial, sans-serif;
  }
  .canvas { position: relative; width: 1200px; height: 750px; }

  .card {
    position: absolute; top: 228px;
    width: 461px; height: 263px;
    overflow: hidden;
  }
  .card--front { left: 124px; background: var(--card-white); }
  .card--back  { left: 618px; background: var(--brand-blue); }

  /* Brand lockup */
  .brand {
    position: absolute; left: 110px; top: 47px;
    width: 245px;
    display: flex; align-items: center; gap: 10px;
  }
  .brand__dot {
    width: 46px; height: 46px; border-radius: 50%; flex: none;
    border: 3px solid var(--brand-blue);
  }
  .brand__name {
    color: var(--brand-blue); font-weight: 400;
    font-size: 12px; line-height: 1.35; letter-spacing: 0.6px;
    text-transform: uppercase; white-space: nowrap;
  }

  /* Person */
  .person { position: absolute; left: 27px; top: 150px; }
  .person__name {
    color: var(--brand-blue); font-weight: 600; font-size: 17px;
    line-height: 22px; text-transform: uppercase;
  }
  .person__title { color: var(--accent-blue); font-size: 13px; line-height: 18px; }
  .person__rule {
    width: 20px; height: 1px; background: var(--rule-grey);
    margin: 9px 0 8px;
  }
  .person__address { color: var(--text-grey); font-size: 12.5px; line-height: 18px; }

  /* Contact list */
  .contacts {
    position: absolute; right: 28px; top: 153px;
    list-style: none; text-align: right;
  }
  .contacts__item {
    display: flex; justify-content: flex-end; align-items: center; gap: 6px;
    color: var(--text-grey); font-size: 12.5px; line-height: 17.6px;
    white-space: nowrap;
  }
  .contacts__icon { width: 12px; height: 12px; fill: var(--brand-blue); flex: none; }

  /* Back */
  .back__pattern {
    position: absolute; inset: 0;
    background: radial-gradient(circle at 50% 50%, var(--pattern-blue), var(--brand-blue));
  }
  .back__mark {
    position: absolute; left: 189px; top: 87px;
    width: 86px; height: 86px; border-radius: 50%;
    border: 4px solid var(--white);
  }
  .back__web {
    position: absolute; left: 0; right: 0; top: 216px;
    text-align: center; color: var(--white);
    font-size: 13px; letter-spacing: 7px; white-space: nowrap;
  }
</style>
</head>
<body>
<main class="canvas">

  <section class="card card--front" aria-label="Business card front">
    <div class="brand">
      <span class="brand__dot"></span>
      <span class="brand__name">Northgate<br>Construction Management</span>
    </div>

    <div class="person">
      <p class="person__name">Daniel Reyes</p>
      <p class="person__title">CEO/Founder</p>
      <div class="person__rule"></div>
      <p class="person__address">2140 Harbor View Road<br>Juneau, Alaska 99801</p>
    </div>

    <ul class="contacts">
      <li class="contacts__item">907 555 0142
        <svg class="contacts__icon" viewBox="0 0 12 12"><path d="M2.5 0.8l2 2.2-1 1.4c.6 1.5 1.6 2.5 3.1 3.1l1.4-1 2.2 2-1 1.9C5 10.4 1.6 7 0.6 1.8z"/></svg>
      </li>
      <li class="contacts__item">907 555 0187
        <svg class="contacts__icon" viewBox="0 0 12 12"><path d="M3 0h6v12H3zM4.2 1.3v8.5h3.6V1.3z"/></svg>
      </li>
      <li class="contacts__item">907 555 0163
        <svg class="contacts__icon" viewBox="0 0 12 12"><path d="M3 0h6v4H3zM0 5h12v5H0zM3 9h6v3H3z"/></svg>
      </li>
      <li class="contacts__item">contact@northgatecm.com
        <svg class="contacts__icon" viewBox="0 0 12 12"><path d="M0 2h12v8H0zM1.2 3.2v.3L6 6.6l4.8-3.1v-.3z"/></svg>
      </li>
      <li class="contacts__item">www.northgatecm.com
        <svg class="contacts__icon" viewBox="0 0 12 12"><circle cx="6" cy="6" r="5.5"/><path d="M0.5 6h11M6 0.5c-2.5 3-2.5 8 0 11M6 0.5c2.5 3 2.5 8 0 11" stroke="#fbfbfb" stroke-width="0.8" fill="none"/></svg>
      </li>
    </ul>
  </section>

  <section class="card card--back" aria-label="Business card back">
    <div class="back__pattern" role="img" aria-label="Repeating pattern of the company emblem in soft blue tones"></div>
    <span class="back__mark"></span>
    <p class="back__web">www.northgatecm.com</p>
  </section>

</main>
</body>
</html>
```